Business Card Design

Hi I need a business card designed, we already have the business name logo artwork and would like some concept ideas for the Bus Card layout.
On the back of the card i want to include the products and services that we offer.
We are a Plastics Sheeting manufacture based in Perth Australia.

                                       

We need a BC design for a company called Tarvo Plastics based in Perth Australia.

We supply from DIY to Trade & Industrial  Engineering Markets.

We specialise in:

·         Cut to size panels  (all shapes and sizes)

·         Plastics fabrication & Welding

·         Custom Designs

·         Plastic Repairs

·         PVC Pipe Slotting & PVC Pipe Threading

·         Supplier of all types of engineering plastics and profiles.

Including:           Acrylic / Clarvene

                               Polycarbonate / Dorvil

                               Prismatic Light Diffuser

                               Vantrib

                               HDPE / UHMWPE

                               PVC / PVC Foam

                               Nylon

                               HIPS

```html
<!DOCTYPE html>
<html lang="en">
<head>
<meta charset="utf-8">
<title>Tarvo Plastics – Business Card</title>
<link href="https://fonts.googleapis.com/css2?family=Open+Sans:wght@400;600;700;800&display=swap" rel="stylesheet">
<style>
  :root {
    --navy: #1e2a6e;
    --blue: #1f6fb8;
    --orange: #ee8a2e;
    --grey: #4a4a4a;
    --card: #ffffff;
    --backdrop: #ececec;
  }
  * { box-sizing: border-box; margin: 0; padding: 0; }
  html, body { width: 1200px; height: 720px; overflow: hidden; }
  body {
    background: var(--backdrop);
    font-family: "Open Sans", Arial, sans-serif;
    position: relative;
  }
  .card {
    position: absolute;
    width: 560px;
    height: 320px;
    background: var(--card);
    box-shadow: 0 4px 14px rgba(0,0,0,0.12);
  }
  .card--front { left: 30px; top: 200px; }
  .card--back { left: 610px; top: 200px; }

  /* Front */
  .brand {
    position: absolute;
    left: 40px; top: 40px;
    display: flex; align-items: center; gap: 12px;
  }
  .brand__mark { width: 22px; height: 22px; background: var(--navy); }
  .brand__name {
    font-size: 44px; font-weight: 800; color: var(--navy);
    letter-spacing: -0.5px; line-height: 1;
  }
  .person { position: absolute; left: 40px; top: 168px; color: var(--grey); }
  .person__name { font-size: 19px; font-weight: 700; color: var(--navy); line-height: 1.2; }
  .person__title { font-size: 13px; color: var(--orange); margin-bottom: 8px; }
  .person__address { font-size: 13px; line-height: 1.4; margin-bottom: 8px; }

  .contact {
    position: absolute; left: 318px; top: 124px;
    padding-left: 14px; border-left: 1.5px solid var(--orange);
    height: 140px; font-size: 12.5px; color: var(--grey);
  }
  .contact__row { display: flex; align-items: center; gap: 7px; line-height: 1.55; }
  .contact__row svg { width: 11px; height: 11px; fill: var(--navy); flex: none; }
  .contact__company { margin-top: 8px; line-height: 1.35; }

  /* Back */
  .offer { position: absolute; inset: 0; padding: 30px 30px; text-align: center; color: var(--navy); }
  .offer__intro { font-size: 15px; font-weight: 700; line-height: 1.3; }
  .offer__heading { font-size: 17px; font-weight: 700; margin: 12px 0 6px; }
  .offer__list {
    list-style: none; font-size: 12.5px; color: var(--grey); line-height: 1.6;
    display: flex; flex-wrap: wrap; justify-content: center; column-gap: 14px;
  }
  .offer__list li::before {
    content: ""; display: inline-block; width: 5px; height: 5px;
    border-radius: 50%; background: var(--blue);
    margin-right: 5px; vertical-align: middle;
  }
  .offer__list--services { max-width: 440px; margin: 0 auto; }
  .offer__list--materials { max-width: 400px; margin: 0 auto; }
</style>
</head>
<body>

<section class="card card--front" aria-label="Business card front">
  <div class="brand">
    <span class="brand__mark"></span>
    <span class="brand__name">Tarvo Plastics</span>
  </div>

  <div class="person">
    <p class="person__name">Your Name</p>
    <p class="person__title">Title</p>
    <p class="person__address">Unit 4/18 Brookfield Loop<br>Marlow Park WA 6162</p>
    <p class="person__address">PO Box 2384<br>Marlow Park DC WA 6963</p>
  </div>

  <div class="contact">
    <p class="contact__row">
      <svg viewBox="0 0 12 12" aria-hidden="true"><path d="M2.5 1 4.5 3 3.6 4.4c.6 1.6 2.3 3.3 3.9 3.9L9 7.5l2 2-1.4 1.6C5.4 11 1 6.6.9 2.4Z"/></svg>
      08 9471 3305
    </p>
    <p class="contact__row">
      <svg viewBox="0 0 12 12" aria-hidden="true"><rect x="3" y="0.5" width="6" height="11" rx="1"/><rect x="4" y="2" width="4" height="6" fill="#fff"/></svg>
      0400 218 764
    </p>
    <p class="contact__row">
      <svg viewBox="0 0 12 12" aria-hidden="true"><rect x="3" y="1" width="6" height="4"/><rect x="1" y="5" width="10" height="6" rx="1"/><rect x="3" y="7" width="6" height="1.2" fill="#fff"/></svg>
      08 9471 3306
    </p>
    <p class="contact__row">
      <svg viewBox="0 0 12 12" aria-hidden="true"><rect x="0.5" y="2" width="11" height="8" rx="1"/><path d="M1 2.6 6 6.6 11 2.6" fill="none" stroke="#fff" stroke-width="1.2"/></svg>
      sales@tarvoplastics.com.au
    </p>
    <p class="contact__company">Tarvo Holdings Pty Ltd<br>T/A Tarvo Plastics ABN: TBA</p>
  </div>
</section>

<section class="card card--back" aria-label="Business card back">
  <div class="offer">
    <p class="offer__intro">The Products And Services That We Offer<br>Are Supplied From DIY To Trade &amp; Industrial Engineering Markets</p>

    <h2 class="offer__heading">We specialise in:</h2>
    <ul class="offer__list offer__list--services">
      <li>Cut to size panels (all shapes and sizes)</li>
      <li>Plastics fabrication &amp; Welding</li>
      <li>Custom Designs</li>
      <li>Plastic Repairs</li>
      <li>PVC Pipe Slotting &amp; PVC Pipe Threading</li>
      <li>Supplier of all types of engineering plastics and profiles</li>
    </ul>

    <h2 class="offer__heading">Including:</h2>
    <ul class="offer__list offer__list--materials">
      <li>Acrylic / Clarvene</li>
      <li>Polycarbonate / Dorvil</li>
      <li>Prismatic Light Diffuser</li>
      <li>Vantrib</li>
      <li>HDPE / UHMWPE</li>
      <li>PVC / PVC Foam</li>
      <li>Nylon</li>
      <li>HIPS</li>
    </ul>
  </div>
</section>

</body>
</html>
```